Facebook & Instagram Design for: The Ledger of Pim - Paws of Quiet Hound

Need a Facebook Page and Instagram Page too for helping launch a book as a brand new author with a book on my old dog Pim and the Zen lessons he taught me.
Its all for folks who love dogs and especially rescue dog stories
Its all for folks who are interested in something slightly spiritual and for self growth
I attach the review copy from my publishers who are standing up a website but recommend a Facebook Page that is attached to my own personal one and an Instagram Page
I intend on publishing weekly "Pimtricks" (The dog was called Pim)
I intend on posting Zen talks (in lay man's terms)
I have a second book being written to follow on the one
Myself as an Author needs profiling
The book needs ALOT of promotion - and we can't travel!
I need to host a bunch of "book talks/launches"
Need to send folks to my website to by the book: Hard/Paperback/Lumera - which comes with book trailer
I have hundreds of photos to give
I have alot of sketches of the dog to share which did not make it into the book
My competition are books like:
Hollis & Us
A Cat naps int Caring Lodge
Tuxa
The Baron's Beagle
A Pups Journey
Need this ASAP - publishing date is moved up to October 2021!
Link t Author hot File Crate: https://www.filecrate.example/sh/kqwplm2231907t4/AAFhtrWmnPqLsKe7vb_XoPla?dl=0
Link to Dog Photos:
https://www.filecrate.example/sh/mvbtr83knwoz02/AAC4j1hnqe_k5Rs9WYpoltQ2m?dl=0
Updates
Hello, I will be in hospitaal having surgery on my neck and request tow more days to =make any kind of small changes. Thank you Marisol
Target Market(s)
Dog owners around the world, especially those wth rescue dogs and those looking for personal growth and those interested in Zen Buddhism
Industry/Entity Type
Author promoting soon to be published book/s
Requirements
Must have
- Author Photo/E-Mail Sign Up/Link to Instagram (see brief to design this)/Link to upcoming website/Link to Writer Hub (might need to design me something)/Photo Gallery
Nice to have
- Author features and Dog Images (I have new dogs we can show)
Should not have
- Cute - its a meaningful book

```html
<!DOCTYPE html>
<html lang="en">
<head>
<meta charset="utf-8">
<title>The Ledger of Pim – Social Posts</title>
<link rel="stylesheet" href="https://fonts.googleapis.com/css2?family=Montserrat:wght@500;600;700;800&family=Satisfy&family=Great+Vibes&display=swap">
<style>
  :root{
    --page:#b9c9d3;
    --cyan:#1a9bd7;
    --violet:#4a3fc6;
    --navy:#1d2440;
    --sky-top:#f3eee4;
    --sky-mid:#dfe6ea;
    --cloud:#eef2f4;
    --cloud-shade:#c7d2da;
    --ring-a:#3b3bb8;
    --ring-b:#a06ad8;
    --cover:#1d4fb0;
    --cover-deep:#10307a;
    --white:#ffffff;
  }
  *{margin:0;padding:0;box-sizing:border-box}
  html,body{width:923px;height:1200px;overflow:hidden;background:var(--page)}
  .canvas{position:relative;width:923px;height:1200px;font-family:"Montserrat",sans-serif}
  .post{position:absolute;width:376px;height:376px;overflow:hidden;box-shadow:0 2px 6px rgba(0,0,0,.25)}
  .post--rescued{left:79px;top:24px}
  .post--writer{left:469px;top:24px}
  .post--cover{left:79px;top:414px}
  .post--date{left:469px;top:414px}
  .post--wisdom{left:79px;top:806px}
  .post--comfort{left:469px;top:806px}

  .sky{position:absolute;inset:0;
    background:linear-gradient(180deg,var(--sky-top) 0%,var(--sky-mid) 45%,var(--cloud-shade) 62%,var(--cloud) 78%,#f6f8f9 100%)}
  .sky--violet{background:linear-gradient(180deg,#7b6fd3 0%,#b7a9e6 28%,#dcd6ee 48%,var(--cloud-shade) 68%,var(--cloud) 100%)}
  .sky--grey{background:linear-gradient(180deg,#eef0f2 0%,#e2e6e9 40%,var(--cloud-shade) 65%,var(--cloud) 100%)}

  .quote{position:absolute;font-weight:700;line-height:1.25;
    background:linear-gradient(180deg,var(--cyan),var(--violet));
    -webkit-background-clip:text;background-clip:text;color:transparent}
  .quote .mark{font-weight:800}

  .quote--rescued{left:0;right:0;top:74px;text-align:center;font-size:20.5px;line-height:1.28}
  .quote--wisdom{left:31px;top:72px;font-size:22.5px;line-height:1.38}
  .quote--comfort{left:30px;top:44px;font-size:21px;line-height:1.35}

  .writer-kicker{position:absolute;left:0;right:0;top:20px;text-align:center;color:var(--navy);font-weight:500;font-size:15px;line-height:1.45}
  .writer-headline{position:absolute;left:0;right:0;top:72px;text-align:center;color:var(--cyan);font-weight:700;font-size:21px;line-height:1.7}
  .writer-headline .name{font-size:34px;font-weight:800;line-height:1}

  .ring{position:absolute}
  .photo{position:absolute}
  .photo--writer{left:107px;top:172px;width:164px;height:164px;border-radius:50%;
    background:radial-gradient(circle at 45% 40%,#d8d8d8,#8a8a8a 60%,#4a4a4a)}

  .title{position:absolute;left:0;right:0;top:36px;text-align:center;font-weight:800;color:var(--cyan);letter-spacing:.5px}
  .title .small{font-size:22px}
  .title .big{font-size:50px;line-height:1;color:#1c8fd6}
  .subtitle{position:absolute;left:0;right:0;top:88px;text-align:center;font-family:"Satisfy",cursive;font-size:24px;color:var(--navy)}
  .byline{position:absolute;left:70px;top:132px;font-size:11.5px;font-weight:700;color:var(--navy);letter-spacing:.3px}
  .photo--author{left:0;top:156px;width:276px;height:220px;
    background:linear-gradient(100deg,#b52245 0%,#c43b5a 38%,#a37a55 60%,#7a5a3c 100%);
    border-top-right-radius:140px}
  .coming{position:absolute;left:36px;top:306px;color:var(--white);font-size:21px;font-weight:500;display:flex;align-items:baseline}
  .coming .soon{font-family:"Great Vibes",cursive;font-size:46px;margin-left:2px}

  .book{position:absolute;background:linear-gradient(160deg,var(--cover) 0%,#2a6fd0 45%,var(--cover-deep) 100%);
    color:var(--white);box-shadow:3px 4px 10px rgba(0,0,0,.3)}
  .book .b-title{position:absolute;left:10%;top:6%;font-weight:800;line-height:1.05}
  .book .b-sub{position:absolute;left:10%;font-family:"Satisfy",cursive;color:#dfe9ff}
  .book .b-art{position:absolute;left:0;right:0;background:linear-gradient(180deg,#8fc4e6,#6f9b52 45%,#7a5a3e 100%)}
  .book .b-author{position:absolute;left:0;right:0;text-align:center;letter-spacing:1.5px;font-weight:600}

  .book--main{left:113px;top:66px;width:169px;height:258px}
  .book--main .b-title{font-size:19px}
  .book--main .b-title .big{font-size:40px}
  .book--main .b-sub{top:40%;font-size:15px}
  .book--main .b-art{top:50%;height:36%}
  .book--main .b-author{bottom:10px;font-size:13px}

  .book--side{left:-14px;top:248px;width:96px;height:150px;transform:rotate(22deg)}
  .book--side .b-title{font-size:10px}
  .book--side .b-title .big{font-size:20px}
  .book--side .b-sub{top:38%;font-size:8px}
  .book--side .b-art{top:48%;height:34%}
  .book--side .b-author{bottom:5px;font-size:7px}

  .book--peek{left:336px;top:232px;width:90px;height:140px;transform:rotate(24deg)}
  .book--peek .b-title{font-size:9px}
  .book--peek .b-title .big{font-size:19px}
  .book--peek .b-sub{top:38%;font-size:8px}
  .book--peek .b-art{top:48%;height:34%}
  .book--peek .b-author{bottom:5px;font-size:7px}

  .date-pill{position:absolute;left:65px;top:25px;width:246px;height:32px;border-radius:16px;background:var(--cyan);
    color:var(--white);font-weight:700;font-size:22px;letter-spacing:1.5px;text-align:center;line-height:32px}

  .photo--dog{left:0;top:150px;width:376px;height:226px;
    background:linear-gradient(180deg,rgba(238,240,242,0) 0%,#9a9a9a 30%,#5c5c5c 70%,#3c3c3c 100%)}
</style>
</head>
<body>
<main class="canvas">

  <section class="post post--rescued">
    <div class="sky" role="img" aria-label="Mountain peak rising above a sea of clouds"></div>
    <p class="quote quote--rescued"><span class="mark">❝</span> For The Rescued And<br>The Rescuers<br>For Whom Love is Always<br>The Answer And<br>The Answer, Always Love <span class="mark">❞</span></p>
  </section>

  <section class="post post--writer">
    <div class="sky" role="img" aria-label="Soft clouds at dawn"></div>
    <p class="writer-kicker">Firs-time Writer<br>-Marisol Vantree</p>
    <p class="writer-headline">Recalls Her Adventures<br>of Her Rescue Dog,<span class="name">Pim</span></p>
    <div class="photo photo--writer" role="img" aria-label="Black and white photo of the author resting beside her dog Pim"></div>
    <svg class="ring" style="left:83px;top:148px" width="212" height="212" viewBox="0 0 212 212" aria-hidden="true">
      <defs><linearGradient id="ringA" x1="0" y1="1" x2="1" y2="0"><stop offset="0" stop-color="var(--ring-a)"/><stop offset="1" stop-color="var(--ring-b)"/></linearGradient></defs>
      <circle cx="106" cy="106" r="92" fill="none" stroke="url(#ringA)" stroke-width="9" stroke-dasharray="520 60" transform="rotate(-70 106 106)"/>
    </svg>
  </section>

  <section class="post post--cover">
    <div class="sky sky--violet" role="img" aria-label="Violet sky fading into clouds"></div>
    <h2 class="title"><span class="small">THE LEDGER of </span><span class="big">PIM</span></h2>
    <p class="subtitle">Paws of Quiet Hound</p>
    <p class="byline">— MARISOL VANTREE</p>
    <svg class="ring" style="left:60px;top:150px" width="270" height="270" viewBox="0 0 270 270" aria-hidden="true">
      <defs><linearGradient id="ringB" x1="0" y1="0" x2="1" y2="1"><stop offset="0" stop-color="var(--ring-b)"/><stop offset="1" stop-color="var(--ring-a)"/></linearGradient></defs>
      <circle cx="135" cy="135" r="118" fill="none" stroke="url(#ringB)" stroke-width="10" stroke-dasharray="420 320" transform="rotate(-150 135 135)"/>
    </svg>
    <div class="photo photo--author" role="img" aria-label="The author in a red coat kneeling beside her brindle dog"></div>
    <div class="book book--peek" role="img" aria-label="The Ledger of Pim book cover">
      <div class="b-title">THE LEDGER<br>of <span class="big">PIM</span></div>
      <div class="b-sub">Paws of Quiet Hound</div>
      <div class="b-art"></div>
      <div class="b-author">MARISOL VANTREE</div>
    </div>
    <p class="coming">Coming<span class="soon">Soon</span></p>
  </section>

  <section class="post post--date">
    <div class="sky sky--grey" role="img" aria-label="Snowy peaks among clouds"></div>
    <p class="date-pill">OCTOBER 2021</p>
    <div class="book book--side" role="img" aria-label="The Ledger of Pim book, tilted">
      <div class="b-title">THE LEDGER<br>of <span class="big">PIM</span></div>
      <div class="b-sub">Paws of Quiet Hound</div>
      <div class="b-art"></div>
      <div class="b-author">MARISOL VANTREE</div>
    </div>
    <div class="book book--main" role="img" aria-label="The Ledger of Pim book with cover photo of the dog among flowers">
      <div class="b-title">THE LEDGER<br>of <span class="big">PIM</span></div>
      <div class="b-sub">Paws of Quiet Hound</div>
      <div class="b-art"></div>
      <div class="b-author">MARISOL VANTREE</div>
    </div>
  </section>

  <section class="post post--wisdom">
    <div class="sky" role="img" aria-label="Mountain peak rising above a sea of clouds"></div>
    <p class="quote quote--wisdom"><span class="mark">❝</span> Zen Wisdom,<br>&nbsp;&nbsp;&nbsp;All True Tails,<br>&nbsp;&nbsp;&nbsp;Dog Wisdom, Lessons<br>&nbsp;&nbsp;&nbsp;on Human Life <span class="mark">❞</span></p>
  </section>

  <section class="post post--comfort">
    <div class="sky sky--grey" aria-hidden="true"></div>
    <div class="photo photo--dog" role="img" aria-label="Black and white photo of Pim resting his head among cushions"></div>
    <p class="quote quote--comfort"><span class="mark">❝</span> It's What Feels<br>&nbsp;&nbsp;&nbsp;&nbsp;Comfortable<br>&nbsp;&nbsp;&nbsp;&nbsp;That Makes Your<br>&nbsp;&nbsp;&nbsp;&nbsp;Practice Comfortable <span class="mark">❞</span></p>
  </section>

</main>
</body>
</html>
```